Business card design Needed for new logo / Construction business, home extensions and new builds

We need a business card design using our new logo files which i will attach to this project :)

We are a small construction business specialising in home extensions, new builds and property development. We are very ambitious and would appreciate professional and elegant designs for our new business card.

Very serious about using the services on MakerQuarry and recently acquired our new logo from here :)

Please get involved, i will feedback when i can as i am very busy but can respond daily, thanks

Target Market(s)

People that want to build onto their houses, new building developments or adding too their existing property

Industry/Entity Type

Construction

Contact Information for Business Card

Renwick Tolliver Construction, Lionel Ashby (Managing Director), Tel 07822254961, email - info@renwick-tolliver, www.renwick-tolliver.co.uk

Colors

Designer to choose colors to be used in the design.

Requirements
Must have
• I like a deep grey on the back please. A lot of you have provided black from and back, try mixing things up a little. The black looks cool 😎 Thanks

```html
<!DOCTYPE html>
<html lang="en">
<head>
<meta charset="utf-8">
<title>Renwick Tolliver Construction – Business Card</title>
<link rel="stylesheet" href="https://fonts.googleapis.com/css2?family=Open+Sans:wght@400;600;700&display=swap">
<style>
  :root {
    --stage: #222223;
    --card: #1e1e21;
    --card-back: #161618;
    --gold: #d9a21e;
    --gold-light: #f1c65a;
    --silver: #c9cbcf;
    --white: #f4f4f4;
    --ghost: #2c2c30;
  }
  * { margin: 0; padding: 0; box-sizing: border-box; }
  html, body { width: 1200px; height: 780px; overflow: hidden; background: var(--stage); }
  body { position: relative; font-family: "Open Sans", Arial, sans-serif; }

  .card {
    position: absolute;
    width: 540px;
    height: 310px;
    overflow: hidden;
    box-shadow: 0 18px 40px rgba(0,0,0,.55);
  }
  .card::after {
    content: "";
    position: absolute;
    left: 0; right: 0; bottom: 0;
    height: 5px;
    background: linear-gradient(90deg, #9c6f12, var(--gold-light), var(--gold), #9c6f12);
  }

  /* Back of card */
  .card--back { left: 40px; top: 60px; background: var(--card-back); }
  .card__pattern {
    position: absolute; inset: 0;
    background: linear-gradient(160deg, #3a3a3e 0%, #1d1d20 35%, #131315 100%);
  }
  .card__brand {
    position: absolute; right: 22px; bottom: 26px;
    display: flex; align-items: center; gap: 6px;
    font-size: 8px; font-weight: 600; letter-spacing: .06em;
    color: var(--gold); text-transform: uppercase;
  }
  .card__brand-dot { width: 9px; height: 9px; border-radius: 50%; background: var(--gold); }

  /* Front of card */
  .card--front { left: 620px; top: 410px; background: var(--card); }
  .front__ghost-name {
    position: absolute; left: 40px; bottom: 38px;
    font-size: 40px; font-weight: 700; line-height: 1;
    color: var(--ghost); text-transform: uppercase; letter-spacing: .04em;
  }
  .front__ghost-name span { display: block; margin: 6px 0 0 100px; font-size: 30px; }

  .front__person { position: absolute; left: 38px; top: 112px; }
  .front__name { font-size: 34px; font-weight: 700; line-height: 1; color: var(--silver); }
  .front__name-last { color: var(--gold); }
  .front__role { margin: 6px 0 0 118px; font-size: 15px; font-weight: 600; color: var(--white); }

  .front__divider {
    position: absolute; left: 300px; top: 64px;
    width: 2px; height: 112px; background: var(--white);
  }

  .front__contact { position: absolute; left: 318px; top: 68px; list-style: none; }
  .front__contact li {
    display: flex; align-items: center; gap: 8px;
    margin-bottom: 10px; font-size: 13px; color: var(--white);
  }
  .front__contact svg { width: 14px; height: 14px; flex: none; }

  .front__address {
    position: absolute; left: 130px; top: 218px;
    font-size: 14px; color: var(--white);
  }
</style>
</head>
<body>

  <section class="card card--back" aria-label="Back of business card">
    <div class="card__pattern" role="img" aria-label="Repeating brand pattern on deep grey with a soft sheen"></div>
    <div class="card__brand">
      <span class="card__brand-dot"></span>
      <span>Renwick Tolliver Construction</span>
    </div>
  </section>

  <section class="card card--front" aria-label="Front of business card">
    <p class="front__ghost-name" aria-hidden="true">Renwick Tolliver<span>Construction</span></p>

    <div class="front__person">
      <h1 class="front__name">Lionel <span class="front__name-last">Ashby</span></h1>
      <p class="front__role">Managing Director</p>
    </div>

    <div class="front__divider"></div>

    <ul class="front__contact">
      <li>
        <svg viewBox="0 0 24 24" aria-hidden="true"><path fill="#d9a21e" d="M6.6 10.8a15.1 15.1 0 0 0 6.6 6.6l2.2-2.2a1 1 0 0 1 1-.25 11.4 11.4 0 0 0 3.6.57 1 1 0 0 1 1 1V20a1 1 0 0 1-1 1A17 17 0 0 1 3 4a1 1 0 0 1 1-1h3.5a1 1 0 0 1 1 1c0 1.25.2 2.45.57 3.57a1 1 0 0 1-.25 1z"/></svg>
        <span>0782 225 4961</span>
      </li>
      <li>
        <svg viewBox="0 0 24 24" aria-hidden="true"><circle cx="12" cy="12" r="9" fill="none" stroke="#d9a21e" stroke-width="2"/><path d="M3 12h18M12 3c3 3 3 15 0 18M12 3c-3 3-3 15 0 18" fill="none" stroke="#d9a21e" stroke-width="1.5"/></svg>
        <span>info@renwick-tolliver.co.uk</span>
      </li>
      <li>
        <svg viewBox="0 0 24 24" aria-hidden="true"><rect x="3" y="6" width="18" height="13" fill="none" stroke="#d9a21e" stroke-width="2"/><path d="M3 6l9 7 9-7" fill="none" stroke="#d9a21e" stroke-width="2"/></svg>
        <span>www.renwick-tolliver.co.uk</span>
      </li>
    </ul>

    <p class="front__address">Alder Lane, Westbrook Harbourside, HX4 7QN</p>
  </section>

</body>
</html>
```